Banner ads for LP that work with same theme as below banners

Love the banner ads below. Need more with attached photos. But use the same wording, font as in below banner ads. Should be LP size 1200/627 so I can use for Pixorly and LP. Looking for great ads to use as LP ads. We do lots of ads so it will be worth your time to enter this contest you will be rewarded with a ton of work. Need several banner ads that work together. So maybe 1 of the dresses, 1 of the sweater, 1 of the leggings, 1 of the jacket

Target Market(s)

Women 24-45

Industry/Entity Type

Fashion

Requirements
Must have
• Banner ads that work for LP and Pixorly
Nice to have
• Several options to choose from
Should not have
• not sure

```html
<!DOCTYPE html>
<html lang="en">
<head>
<meta charset="UTF-8">
<title>Winter Wear Collection Banner</title>
<link rel="stylesheet" href="https://fonts.googleapis.com/css2?family=Great+Vibes&family=Playfair+Display:wght@400;700;900&display=swap">
<style>
  :root {
    --night-deep: #14223a;
    --night-mid: #1f2f4c;
    --glow-violet: #6a4f9a;
    --glow-red: #b8283c;
    --glow-amber: #d88a4a;
    --panel-taupe: #86704f;
    --cta-red: #c81f3e;
    --text-light: #ffffff;
    --model-light: #d9cfc6;
    --model-dark: #1c1618;
  }
  * { margin: 0; padding: 0; box-sizing: border-box; }
  html, body { width: 1200px; height: 627px; overflow: hidden; }
  body { background: var(--night-deep); }
  .banner {
    position: relative;
    width: 1200px;
    height: 627px;
    overflow: hidden;
  }
  .city-lights {
    position: absolute;
    inset: 0;
    background:
      radial-gradient(circle at 70% 12%, rgba(230,190,200,.55) 0, transparent 22%),
      radial-gradient(circle at 85% 60%, rgba(184,40,60,.55) 0, transparent 18%),
      radial-gradient(circle at 55% 62%, rgba(184,40,60,.45) 0, transparent 14%),
      radial-gradient(circle at 8% 35%, rgba(216,138,74,.35) 0, transparent 14%),
      radial-gradient(circle at 6% 75%, rgba(200,170,230,.45) 0, transparent 16%),
      radial-gradient(circle at 92% 20%, rgba(106,79,154,.55) 0, transparent 20%),
      linear-gradient(180deg, var(--night-mid) 0%, var(--night-deep) 55%, #2a2346 100%);
  }
  .model {
    position: absolute;
    border-radius: 40% 40% 10% 10% / 12% 12% 4% 4%;
  }
  .model--floral {
    left: 222px; top: 30px; width: 180px; height: 597px;
    background: linear-gradient(180deg, #c9a996 0%, var(--model-light) 35%, #e8e2dc 100%);
  }
  .model--lace {
    left: 400px; top: 36px; width: 175px; height: 591px;
    background: linear-gradient(180deg, #c79a74 0%, #3a2a28 30%, var(--model-dark) 100%);
  }
  .promo-panel {
    position: absolute;
    inset: 0;
  }
  .promo-title {
    position: absolute;
    left: 630px;
    top: 168px;
    width: 420px;
    text-align: center;
    color: var(--text-light);
  }
  .promo-title__script {
    display: block;
    font-family: "Great Vibes", cursive;
    font-size: 64px;
    line-height: 1;
  }
  .promo-title__main {
    display: block;
    font-family: "Playfair Display", serif;
    font-weight: 700;
    font-size: 62px;
    letter-spacing: 3px;
    line-height: 1.05;
    margin-top: 2px;
  }
  .cta-button {
    position: absolute;
    left: 699px;
    top: 338px;
    width: 274px;
    height: 44px;
    background: var(--cta-red);
    color: var(--text-light);
    font-family: "Playfair Display", serif;
    font-size: 22px;
    letter-spacing: 2px;
    display: flex;
    align-items: center;
    justify-content: center;
    gap: 8px;
    text-decoration: none;
  }
  .cta-button strong { font-weight: 900; }
  .cta-button span { font-weight: 400; }
</style>
</head>
<body>
  <main class="banner">
    <div class="city-lights" role="img" aria-label="Blurred night city lights with violet, red and amber bokeh"></div>

    <div class="model model--floral" role="img" aria-label="Model in a sheer floral embroidered maxi dress"></div>
    <div class="model model--lace" role="img" aria-label="Model in a black lace handkerchief-hem dress with lace-up heels"></div>

    <svg class="promo-panel" width="1200" height="627" viewBox="0 0 1200 627" aria-hidden="true">
      <polygon points="574,160 1058,85 1085,325 620,415" fill="var(--panel-taupe)"/>
    </svg>

    <h1 class="promo-title">
      <span class="promo-title__script">Winter Wear</span>
      <span class="promo-title__main">COLLECTION</span>
    </h1>

    <a class="cta-button" href="#"><strong>SHOP</strong><span>THE</span><strong>LOOK</strong></a>
  </main>
</body>
</html>
```